Bramblewood Card Company Business Cards

We are a trading card store with Glimmorax, sports and other TCG cards, we need a business card design that encompasses a clean cut, modern style with a retro flare. website is bramblewoodcardco.com for reference. Can utilize a comic book era feel or a more modern outdoor feel to utilize the "Pacific Northwest" elements of tress, mountains, etc.

Industry/Entity Type

Trading cards and collectibles

Contact Information for Business Card

business name, email address, phone number, name, owner job title

Font styles to use
Sans Serif

```html
<!DOCTYPE html>
<html lang="en">
<head>
<meta charset="utf-8">
<title>Bramblewood Card Company – Business Cards</title>
<link href="https://fonts.googleapis.com/css2?family=Open+Sans:wght@400;600;700&display=swap" rel="stylesheet">
<style>
  :root {
    --stage: #dcdcdb;
    --paper: #f7f7f6;
    --slate: #6d6d6e;
    --ink: #5a5a5c;
    --accent: #1ea6cc;
    --edge: #179bbf;
    --snow: #ffffff;
    --snow-soft: #e4e4e4;
  }
  * { box-sizing: border-box; margin: 0; padding: 0; }
  html, body {
    width: 1200px; height: 810px; overflow: hidden;
    background: var(--stage);
    font-family: "Open Sans", Arial, sans-serif;
  }
  .stage { position: relative; width: 1200px; height: 810px; }

  .card {
    position: absolute;
    width: 520px; height: 297px;
    border-bottom: 4px solid var(--edge);
    box-shadow: 0 6px 18px rgba(0,0,0,0.12);
    overflow: hidden;
  }

  /* Front */
  .card--front { left: 60px; top: 150px; background: var(--paper); }
  .brand-mark {
    position: absolute; right: 40px; top: 46px;
    width: 170px; text-align: center;
    color: var(--ink); font-weight: 700;
    font-size: 17px; line-height: 1.25; letter-spacing: 1px;
    text-transform: uppercase;
  }
  .holder { position: absolute; left: 40px; top: 128px; }
  .holder__name { color: var(--accent); font-weight: 600; font-size: 21px; line-height: 1.1; }
  .holder__title { color: var(--ink); font-size: 13px; margin-top: 2px; }
  .contact { position: absolute; left: 40px; bottom: 30px; list-style: none; }
  .contact__item {
    display: flex; align-items: center; gap: 8px;
    color: var(--ink); font-size: 13px; line-height: 20px;
  }
  .contact__icon { width: 11px; height: 11px; flex: none; }

  /* Back */
  .card--back { left: 620px; top: 360px; background: var(--slate); }
  .brand-mark--back {
    color: var(--snow-soft); left: 40px; right: auto; top: 50px;
    text-align: left;
  }
  .peaks {
    position: absolute; right: 0; bottom: 0;
    width: 210px; height: 200px;
  }
  .web {
    position: absolute; left: 40px; bottom: 38px;
    color: var(--snow); font-size: 15px; letter-spacing: 0.3px;
    white-space: nowrap;
  }
  .web strong { font-weight: 700; }
</style>
</head>
<body>
<main class="stage">

  <section class="card card--front" aria-label="Business card front">
    <div class="brand-mark">Bramblewood<br>Card Company</div>

    <div class="holder">
      <p class="holder__name">Owen Hartley</p>
      <p class="holder__title">Managing Director</p>
    </div>

    <ul class="contact">
      <li class="contact__item">
        <svg class="contact__icon" viewBox="0 0 12 12" aria-hidden="true">
          <circle cx="6" cy="6" r="6" fill="var(--accent)"/>
          <path d="M4 3.2l1.2 1.3-.6.8a4 4 0 0 0 2.1 2.1l.8-.6 1.3 1.2-.7.9C5.9 8.8 3.2 6.1 3.1 3.9z" fill="#fff"/>
        </svg>
        200.555.0140
      </li>
      <li class="contact__item">
        <svg class="contact__icon" viewBox="0 0 12 12" aria-hidden="true">
          <rect x="0.5" y="2" width="11" height="8" rx="1" fill="var(--accent)"/>
          <path d="M1 2.6l5 3.8 5-3.8" stroke="#fff" stroke-width="1" fill="none"/>
        </svg>
        info@bramblewoodcardco.com
      </li>
      <li class="contact__item">
        <svg class="contact__icon" viewBox="0 0 12 12" aria-hidden="true">
          <circle cx="6" cy="6" r="5.5" fill="var(--accent)"/>
          <path d="M0.8 6h10.4M6 0.6c-2.4 2.8-2.4 8 0 10.8M6 0.6c2.4 2.8 2.4 8 0 10.8" stroke="#fff" stroke-width="0.8" fill="none"/>
        </svg>
        www.bramblewoodcardco.com
      </li>
    </ul>
  </section>

  <section class="card card--back" aria-label="Business card back">
    <div class="brand-mark brand-mark--back">Bramblewood<br>Card Company</div>

    <svg class="peaks" viewBox="0 0 210 200" role="img" aria-label="White mountain range silhouette rising along the lower right">
      <defs>
        <linearGradient id="peakTone" x1="0" y1="1" x2="1" y2="0">
          <stop offset="0" stop-color="#f2f2f2"/>
          <stop offset="1" stop-color="#ffffff"/>
        </linearGradient>
      </defs>
      <rect width="210" height="200" fill="url(#peakTone)" opacity="0.9"/>
    </svg>

    <p class="web">www.<strong>bramblewoodcardco</strong>.com</p>
  </section>

</main>
</body>
</html>
```